We need a complete design for our construction company KELTO CONSTRUCTION based in Auckland New Zealand, we need a logo, website, business card, vehicle design etc..
We are a mid to high-end construction company who work mostly on residential projects and some commercial.

What we want to see in the design;
Professional,
Architectural,
Simple,
Alternative,

We want the design to communicate professionalism, high quality wormanship and and quality service.

Target Market(s)

People looking for a quality building/ construction company

Industry/Entity Type

Construction Company

Contact Information for Business Card

KELTO CONSTRUCTION.co.nz
Lino Verasek
lino@keltoconstruction.example.nz
021 5807 462

Logo Text

KELTO CONSTRUCTION

Number of Pages Required

5+ page

Font styles to use
Sans Serif

Colors

Designer to choose colors to be used in the design.

Requirements
Must have
• Must appear high end, professional, quality, be simple, easy to use, give security to potential clients
Nice to have
• high-quality photos of our recent projects
• about us page
• blog page
• contact us page
• high quality content
Should not have
• should not be hard to use and have too much going on.

```html
<!DOCTYPE html>
<html lang="en">
<head>
<meta charset="utf-8">
<title>Kelto Construction</title>
<link rel="stylesheet" href="https://fonts.googleapis.com/css2?family=Montserrat:wght@400;600;700&family=Lato:ital,wght@0,400;0,700;1,400&display=swap">
<style>
:root{
  --gold:#b8913f;
  --gold-dark:#a8822f;
  --charcoal:#323232;
  --ink:#222222;
  --text:#4a4a4a;
  --muted:#5c5c5c;
  --paper:#ffffff;
  --mist:#eeeeee;
  --line:#d6d6d6;
}
*{margin:0;padding:0;box-sizing:border-box}
html,body{width:1200px;height:2970px;overflow:hidden;background:var(--paper)}
body{position:relative;font-family:'Lato',Arial,sans-serif;color:var(--text)}
.abs{position:absolute}
.site-header{left:0;top:0;width:1200px;height:125px;background:var(--charcoal)}
.brand{left:0;top:30px;width:1200px;text-align:center;font-family:'Montserrat',Arial,sans-serif;font-weight:400;font-size:26px;letter-spacing:7px;color:var(--gold)}
.main-nav{left:77px;top:111px;width:1046px;height:53px;background:var(--gold);display:flex;justify-content:center;align-items:center;gap:48px;box-shadow:0 3px 6px rgba(0,0,0,.25);z-index:3}
.main-nav a{color:#fff;text-decoration:none;font-size:16px;letter-spacing:.5px}
.hero{left:0;top:125px;width:1200px;height:584px;background:linear-gradient(100deg,#a9c8e6 0%,#e4ecf3 40%,#dfe4ea 62%,#6e8ba6 78%,#c9a77c 100%)}
.hero-title{left:79px;top:350px;font-family:'Montserrat',Arial,sans-serif;font-weight:700;font-size:62px;line-height:1.2;color:#555}
.hero-arrow{top:402px;width:47px;height:32px;background:#5b5b5b;display:flex;align-items:center;justify-content:center}
.section-title{left:0;width:1200px;text-align:center;font-family:'Montserrat',Arial,sans-serif;font-weight:600;font-size:42px;color:var(--ink)}
.rule{left:580px;width:40px;height:2px;background:var(--gold)}
.intro{left:230px;top:840px;width:740px;text-align:center;font-size:14.5px;line-height:24px;color:var(--text)}
.feature-photo{top:925px;height:198px}
.feature-caption{top:1148px;width:333px;text-align:center;font-size:17px;color:var(--muted)}
.projects{left:0;top:1240px;width:1200px;height:645px;background:linear-gradient(180deg,#505050,#424242 60%,#3c3c3c)}
.project-tile{width:333px;height:208px}
.project-hover{border:2px solid var(--gold);background:rgba(70,70,70,.55);display:flex;flex-direction:column;align-items:center;justify-content:center;gap:8px;color:#fff;font-family:'Lato',Arial,sans-serif;font-weight:700;font-size:25px}
.project-hover-frame{left:8px;top:8px;right:8px;bottom:8px}
.quote-badge{left:564px;top:2035px;width:72px;height:72px;border-radius:50%;background:var(--gold);display:flex;align-items:center;justify-content:center}
.client-name{left:0;top:2132px;width:1200px;text-align:center;font-size:17px;color:var(--muted)}
.testimonial-text{left:200px;top:2170px;width:800px;text-align:center;font-style:italic;font-size:13.5px;line-height:24.5px;color:var(--muted)}
.dots{left:568px;top:2268px;display:flex;gap:9px}
.dot{width:15px;height:15px;border-radius:50%;border:1.5px solid var(--gold)}
.dot.active{background:var(--gold)}
.blog{left:0;top:2344px;width:1200px;height:438px;background:var(--mist)}
.blog-card{top:2479px;width:468px;height:230px;background:#f4f4f4;border:1px solid var(--line)}
.blog-photo{left:0;top:0;width:208px;height:228px}
.date-badge{top:26px;width:62px;height:78px;background:var(--gold);color:#fff;text-align:center;font-family:'Lato',Arial,sans-serif}
.date-badge .day{display:block;font-size:29px;font-weight:700;line-height:40px;margin-top:4px}
.date-badge .month{display:block;font-size:14px;font-weight:700;line-height:18px}
.blog-title{left:234px;top:26px;width:220px;font-weight:700;font-size:18.5px;line-height:27px;color:var(--ink)}
.blog-excerpt{left:234px;top:86px;width:220px;font-size:14px;line-height:24.5px;color:var(--muted)}
.site-footer{left:0;top:2782px;width:1200px;height:188px;background:var(--gold)}
.footer-brand{left:0;top:50px;width:1200px;text-align:center;font-family:'Montserrat',Arial,sans-serif;font-weight:400;font-size:20px;letter-spacing:5px;color:#fff}
.footer-nav{left:0;top:111px;width:1200px;display:flex;justify-content:center;gap:48px}
.footer-nav a{color:#fff;text-decoration:none;font-size:15px}
.copyright{left:0;top:148px;width:1200px;text-align:center;font-size:14.5px;color:#fff}
</style>
</head>
<body>

<header class="abs site-header">
  <div class="abs brand">KELTO CONSTRUCTION</div>
</header>
<nav class="abs main-nav">
  <a href="#">HOME</a><a href="#">ABOUT</a><a href="#">PROJECTS</a><a href="#">BLOG</a><a href="#">CONTACT</a>
</nav>

<section class="abs hero" role="img" aria-label="Engineer in a hard hat reviewing building plans in front of a construction site"></section>
<h1 class="abs hero-title">We Built<br>your Dreams</h1>
<div class="abs hero-arrow" style="left:0">
  <svg width="22" height="14" viewBox="0 0 22 14"><path d="M21 7H4M9 1L2 7l7 6" fill="none" stroke="#ddd" stroke-width="3"/></svg>
</div>
<div class="abs hero-arrow" style="left:1153px">
  <svg width="22" height="14" viewBox="0 0 22 14"><path d="M1 7h17M13 1l7 6-7 6" fill="none" stroke="var(--gold)" stroke-width="3"/></svg>
</div>

<h2 class="abs section-title" style="top:756px">Welcome to Kelto Contstructions</h2>
<div class="abs rule" style="top:820px"></div>
<p class="abs intro">Lorem Ipsum is simply dummy text of the printing and typesetting industry. Lorem Ipsum has been the industry's standard dummy text ever since the 1500s, when an unknown printer took a galley.</p>

<div class="abs feature-photo" style="left:77px;width:333px;background:linear-gradient(135deg,#3d5675,#aab6c4 55%,#e9edf1)" role="img" aria-label="Team gathered around a table reviewing blueprints"></div>
<div class="abs feature-photo" style="left:434px;width:332px;background:linear-gradient(135deg,#c4cdd6,#8b8f62 45%,#c79b6e)" role="img" aria-label="Two builders in hard hats and vests on site"></div>
<div class="abs feature-photo" style="left:788px;width:333px;background:linear-gradient(180deg,#3c3b46,#c77e52 45%,#6a5e5b 70%,#8c8c8e)" role="img" aria-label="Modern building exterior at sunset"></div>
<div class="abs feature-caption" style="left:77px">Communicate professionalism</div>
<div class="abs feature-caption" style="left:434px">High quality wormanship</div>
<div class="abs feature-caption" style="left:788px">And quality service.</div>

<section class="abs projects" role="img" aria-label="Dimmed construction site backdrop"></section>
<h2 class="abs section-title" style="top:1278px;color:#fff">Latest Projects</h2>
<div class="abs rule" style="top:1346px"></div>

<div class="abs project-tile" style="left:77px;top:1374px;background:linear-gradient(135deg,#dfe8ef,#8aa0b8 50%,#3f4a58)" role="img" aria-label="Two engineers with a tablet on site"></div>
<div class="abs project-tile" style="left:434px;top:1374px;background:linear-gradient(180deg,#3d7fc8,#8fb3d4 45%,#4a4a42 70%,#4d7b3a)" role="img" aria-label="Modern house with pool"></div>
<div class="abs project-tile" style="left:788px;top:1374px;background:linear-gradient(135deg,#d8d6d0,#9a8f80)" role="img" aria-label="Bright modern kitchen interior"></div>
<div class="abs project-hover" style="left:796px;top:1382px;width:317px;height:192px">
  <span>Project Name</span>
  <svg width="30" height="30" viewBox="0 0 24 24"><g fill="none" stroke="#fff" stroke-width="2.4" stroke-linecap="round"><path d="M10 14a4 4 0 0 0 5.6 0l3.2-3.2a4 4 0 0 0-5.6-5.6L11.8 6.6"/><path d="M14 10a4 4 0 0 0-5.6 0l-3.2 3.2a4 4 0 0 0 5.6 5.6l1.4-1.4"/></g></svg>
</div>
<div class="abs project-tile" style="left:77px;top:1606px;background:linear-gradient(135deg,#c9d4dd,#b7b24a 50%,#e5e2d6)" role="img" aria-label="Builders reviewing plans on site"></div>
<div class="abs project-tile" style="left:434px;top:1606px;background:linear-gradient(180deg,#3f7fc6,#a4c2dd 40%,#8d5a46 65%,#7a7770)" role="img" aria-label="Brick commercial building"></div>
<div class="abs project-tile" style="left:788px;top:1606px;background:linear-gradient(135deg,#0f3d7d,#6d9fd0 50%,#dbe7f3)" role="img" aria-label="Glass office tower facade"></div>

<h2 class="abs section-title" style="top:1931px">Testimonials</h2>
<div class="abs rule" style="top:1996px"></div>
<div class="abs quote-badge">
  <svg width="30" height="24" viewBox="0 0 30 24"><g fill="#fff"><path d="M1 24V13C1 6 4 2 11 0l1 3C8 5 7 8 7 11h5v13z"/><path d="M17 24V13c0-7 3-11 10-13l1 3c-4 2-5 5-5 8h5v13z"/></g></svg>
</div>
<div class="abs client-name">- Client Name</div>
<p class="abs testimonial-text">Lorem Ipsum is simply dummy text of the printing and typesetting industry. Lorem Ipsum has been the industry's standard dummy text ever since the 1500s, when an unknown printer took a galley of type and scrambled it to make a type specimen book. It has survived not only five centuries, but also the leap into electronic.</p>
<div class="abs dots"><span class="dot active"></span><span class="dot"></span><span class="dot"></span></div>

<section class="abs blog"></section>
<h2 class="abs section-title" style="top:2382px">Latest Blog</h2>
<div class="abs rule" style="top:2449px"></div>

<article class="abs blog-card" style="left:97px">
  <div class="abs blog-photo" style="background:linear-gradient(135deg,#7a5a3c,#d8b35c 45%,#c9c0b2 70%,#4d86b8)" role="img" aria-label="Builder showing plans to a couple"></div>
  <div class="abs date-badge" style="left:146px"><span class="day">29</span><span class="month">APR</span></div>
  <h3 class="abs blog-title">Lorem Ipsum is simply dummy text.</h3>
  <p class="abs blog-excerpt">Lorem Ipsum is simply dummy text of the printing and typesetting industry. Lorem Ipsum has been the industry's standard dummy.</p>
</article>
<article class="abs blog-card" style="left:632px">
  <div class="abs blog-photo" style="background:linear-gradient(180deg,#6f88a8,#a39a94 45%,#7a6a5a 70%,#4f6a3c)" role="img" aria-label="Two storey family home at dusk"></div>
  <div class="abs date-badge" style="left:146px;top:122px"><span class="day">29</span><span class="month">APR</span></div>
  <h3 class="abs blog-title">Lorem Ipsum is simply dummy text.</h3>
  <p class="abs blog-excerpt">Lorem Ipsum is simply dummy text of the printing and typesetting industry. Lorem Ipsum has been the industry's standard dummy.</p>
</article>

<footer class="abs site-footer">
  <div class="abs footer-brand">KELTO CONSTRUCTION</div>
  <nav class="abs footer-nav"><a href="#">Home</a><a href="#">About</a><a href="#">Project</a><a href="#">Blog</a><a href="#">Contact</a></nav>
  <p class="abs copyright">©KELTO CONSTRUCTIONS- 2018. All Rights Reserved.</p>
</footer>

</body>
</html>
```